Business Card Design of an established Waste Management, Plastic Recycling and Renewable Energy Comp

We are looking for business card design for plastic card with holograms (Very similar to credit card). I will provide our logo (Quenbys). So the name on the business card will be our logo )Quenbys) + Environmental next to it, so it will read Quenbys Environmental. The font for Environmental does not to be the same as the font of the logo. The holograms will be used to display ISO14001 Certified (In normal credit card, normally on the holograms, they show nova or kelo). I will post the design requirements from the card printing company very shortly to make sure they can use the design for the plastic card.

Target Market(s)

Companies, Government Organizations, Corporations.

Industry/Entity Type

Business

Contact Information for Business Card

Motto (Under the logo): Clean Work Always
Name: Leopold Maresca; Position: Business Manager; Address: Pelmore Landfill & Recycling Facility, Tressingham Rd, Kestrel Downs, KR 7390; Ph: +61 8 5210 4738; Mob: +61 455 903 172; E: Leo@quenbysenvironmental-mail.com

Requirements
Must have
• Business Names: Quenbys Logo + Environmental word after the logo.
• Motto (Under the logo): Clean Work Always
• All the Business Card Details above.
• Hologram Logo on the lower right corner which says: ISO 14001 Certified.
• Please remember the design will be printed on plastic card Not paper. The plastic crad is the same as credit card. Hope this helps. Thank You

```html
<!DOCTYPE html>
<html lang="en">
<head>
<meta charset="utf-8">
<title>Quenbys Environmental – Business Card</title>
<link rel="stylesheet" href="https://fonts.googleapis.com/css2?family=Source+Sans+3:wght@400;600;700&display=swap">
<style>
  :root {
    --backdrop: #161616;
    --card: #ffffff;
    --accent: #2397d6;
    --accent-deep: #1d4e96;
    --ink: #4a4a4a;
    --ink-soft: #555a60;
    --badge-line: #1a1a1a;
  }
  * { margin: 0; padding: 0; box-sizing: border-box; }
  html, body {
    width: 1200px; height: 900px; overflow: hidden;
    background: var(--backdrop);
    font-family: "Source Sans 3", "Helvetica Neue", Arial, sans-serif;
  }
  .stage { position: relative; width: 1200px; height: 900px; }
  .card {
    position: absolute; top: 170px;
    width: 347px; height: 561px;
    background: var(--card);
  }
  .card--front { left: 259px; }
  .card--back { left: 631px; }

  .tab {
    position: absolute; left: 102px;
    width: 143px; background: var(--accent);
  }
  .tab--top { top: 0; height: 30px; }
  .tab--bottom { bottom: 0; height: 28px; }

  .brand { position: absolute; left: 37px; top: 112px; width: 300px; }
  .brand__mark {
    position: absolute; left: 0; top: 3px;
    width: 72px; height: 72px; border-radius: 50%;
    background: var(--accent);
  }
  .brand__name {
    position: absolute; left: 82px; top: -6px;
    color: var(--ink-soft); font-weight: 600; line-height: 1;
  }
  .brand__word { display: block; font-size: 47px; letter-spacing: 0.6px; }
  .brand__sub { display: block; font-size: 14px; letter-spacing: 2.2px; margin-top: 2px; }
  .brand__motto {
    position: absolute; left: 84px; top: 61px;
    font-size: 9.5px; letter-spacing: 6.6px;
    color: var(--accent); text-transform: uppercase; white-space: nowrap;
  }

  .person { position: absolute; top: 229px; width: 100%; text-align: center; }
  .person__name { font-size: 23px; font-weight: 700; color: var(--accent-deep); line-height: 1.2; letter-spacing: 0.2px; }
  .person__role { font-size: 16.3px; color: var(--ink); line-height: 1.2; }

  .contacts { position: absolute; top: 301px; width: 100%; list-style: none; text-align: center; }
  .contacts li {
    font-size: 16.3px; color: var(--ink); line-height: 23.5px;
    display: flex; justify-content: center; align-items: center; gap: 6px;
  }
  .contacts svg { fill: var(--accent-deep); flex: none; }

  .address {
    position: absolute; top: 398px; width: 100%;
    text-align: center; font-size: 16px; line-height: 20.5px;
    color: var(--ink); font-style: normal;
  }

  .emblem {
    position: absolute; left: 42px; top: 88px;
    width: 264px; height: 264px; border-radius: 50%;
    background: var(--accent);
    display: flex; align-items: center; justify-content: center;
    color: #ffffff; font-size: 40px; font-weight: 600;
  }
  .hologram {
    position: absolute; left: 131px; top: 403px;
    width: 86px; height: 70px;
    border: 2px solid var(--badge-line); border-radius: 7px;
    display: flex; align-items: center; justify-content: center;
  }
  .hologram__seal {
    width: 54px; height: 54px; border-radius: 50%;
    border: 2px solid var(--badge-line);
  }
</style>
</head>
<body>
<main class="stage">
  <section class="card card--front" aria-label="Business card front">
    <div class="tab tab--top"></div>

    <header class="brand">
      <span class="brand__mark" aria-hidden="true"></span>
      <h1 class="brand__name">
        <span class="brand__word">Quenbys</span>
        <span class="brand__sub">ENVIRONMENTAL</span>
      </h1>
      <p class="brand__motto">Clean work always</p>
    </header>

    <div class="person">
      <h2 class="person__name">Leopold Maresca</h2>
      <p class="person__role">Business Manager</p>
    </div>

    <ul class="contacts">
      <li>
        <svg width="12" height="12" viewBox="0 0 24 24" aria-hidden="true"><path d="M6.6 10.8a15 15 0 0 0 6.6 6.6l2.2-2.2a1 1 0 0 1 1-.25 11.4 11.4 0 0 0 3.6.57 1 1 0 0 1 1 1V20a1 1 0 0 1-1 1A17 17 0 0 1 3 4a1 1 0 0 1 1-1h3.5a1 1 0 0 1 1 1c0 1.25.2 2.45.57 3.57a1 1 0 0 1-.25 1z"/></svg>
        4738 5210 8 +61
      </li>
      <li>
        <svg width="10" height="13" viewBox="0 0 10 16" aria-hidden="true"><path d="M2 0h6a2 2 0 0 1 2 2v12a2 2 0 0 1-2 2H2a2 2 0 0 1-2-2V2a2 2 0 0 1 2-2zm0 2v10h6V2zm3 11a1 1 0 1 0 0 2 1 1 0 0 0 0-2z"/></svg>
        172 903 455 +61
      </li>
      <li>
        <svg width="11" height="8" viewBox="0 0 22 16" aria-hidden="true"><path d="M0 0h22v16H0zm2 2v.5l9 6 9-6V2z"/></svg>
        Leo@quenbysenvironmental-mail.com
      </li>
    </ul>

    <address class="address">
      Pelmore Landfill &amp; Recycling<br>
      Facility Tressingham Rd, Kestrel<br>
      Downs, KR 7390
    </address>

    <div class="tab tab--bottom"></div>
  </section>

  <section class="card card--back" aria-label="Business card back">
    <div class="emblem">Quenbys</div>
    <div class="hologram" aria-label="Certification hologram">
      <span class="hologram__seal"></span>
    </div>
  </section>
</main>
</body>
</html>
```